Satchel & Sundial needs new business card design

I need a new business card design. I'm looking for out-of-the-box design which represents the freedom of being a location independent entrepreneur.
I offer coaching, retreats and trips.
I would like to see designs with and without the photo.
Colors I use are black (#000000), green (#25A796) and brown (#D7C38C)
Website satchelandsundial.example

Target Market(s)

location independent entrepreneurs, digital nomads, people looking to swap the 9 to 5 for a lifestyle business

Industry/Entity Type

Business

Contact Information for Business Card

Dorota Falkner
Your Lifestyle Business Coach, Retreat & Trip Leader
http://satchelandsundial.example
hello@satchelandsundial.example
Live a life you don't need a holiday from

Font styles to use
Serif
Sans Serif

Requirements
Must have
• One side should contain only the logo. I would also consider having the "Live a life you don't need a holiday from" on that side too (depending on how it looks)
• Please show both sides on the designs.

```html
<!DOCTYPE html>
<html lang="en">
<head>
<meta charset="utf-8">
<title>Satchel &amp; Sundial — Business Card</title>
<link rel="stylesheet" href="https://fonts.googleapis.com/css2?family=Open+Sans:wght@400;600;700&display=swap">
<style>
  :root {
    --backdrop: #2a2a2c;
    --card-white: #ffffff;
    --brand-green: #25a796;
    --ink: #2b2b2b;
    --ink-soft: #555555;
    --on-green: #ffffff;
  }
  * { box-sizing: border-box; margin: 0; padding: 0; }
  html, body {
    width: 1200px;
    height: 950px;
    overflow: hidden;
    background: var(--backdrop);
    font-family: "Open Sans", Arial, sans-serif;
  }
  .sheet {
    width: 1200px;
    height: 950px;
    display: flex;
    flex-direction: column;
    align-items: center;
    justify-content: center;
    gap: 40px;
  }
  .card {
    position: relative;
    width: 700px;
    height: 400px;
    overflow: hidden;
    box-shadow: 0 10px 30px rgba(0,0,0,0.35);
  }

  /* Front side */
  .card--front { background: var(--card-white); color: var(--ink); }
  .front-wordmark {
    position: absolute;
    top: 62px;
    right: 48px;
    font-size: 40px;
    font-weight: 700;
    letter-spacing: 1px;
    text-transform: uppercase;
    color: var(--ink);
  }
  .front-rule {
    position: absolute;
    top: 132px;
    left: 300px;
    right: 40px;
    height: 2px;
    background: var(--brand-green);
  }
  .contact-block {
    position: absolute;
    left: 44px;
    bottom: 48px;
  }
  .person-name {
    font-size: 24px;
    font-weight: 600;
    color: var(--brand-green);
    margin-bottom: 6px;
  }
  .person-role {
    font-size: 16px;
    color: var(--ink);
    margin-bottom: 14px;
  }
  .contact-rule {
    width: 400px;
    height: 1px;
    background: var(--brand-green);
    margin-bottom: 12px;
  }
  .contact-line {
    font-size: 12.5px;
    color: var(--ink-soft);
  }
  .contact-label {
    font-weight: 700;
    color: var(--brand-green);
  }
  .contact-line .gap { display: inline-block; width: 12px; }

  /* Back side */
  .card--back { background: var(--brand-green); color: var(--on-green); }
  .back-wordmark {
    position: absolute;
    top: 120px;
    left: 0;
    right: 0;
    text-align: center;
    font-size: 52px;
    font-weight: 700;
    letter-spacing: 1px;
    text-transform: uppercase;
    color: var(--on-green);
  }
  .back-footer {
    position: absolute;
    left: 40px;
    right: 40px;
    bottom: 40px;
    display: flex;
    align-items: center;
    gap: 14px;
  }
  .social-set { display: flex; gap: 4px; }
  .social-set svg { display: block; }
  .tagline {
    font-size: 13px;
    font-style: italic;
    white-space: nowrap;
  }
  .footer-rule {
    flex: 1;
    height: 1px;
    background: var(--on-green);
    opacity: 0.8;
  }
</style>
</head>
<body>
<main class="sheet">

  <section class="card card--front" aria-label="Business card, front">
    <div class="front-wordmark">Satchel &amp; Sundial</div>
    <div class="front-rule"></div>
    <div class="contact-block">
      <p class="person-name">Dorota Falkner</p>
      <p class="person-role">Your Lifestyle Business Coach Retreat &amp; Trip Leader</p>
      <div class="contact-rule"></div>
      <p class="contact-line">
        <span class="contact-label">Email :</span> hello@satchelandsundial.example
        <span class="gap"></span>
        <span class="contact-label">Web :</span> www.satchelandsundial.example
      </p>
    </div>
  </section>

  <section class="card card--back" aria-label="Business card, back">
    <div class="back-wordmark">Satchel &amp; Sundial</div>
    <div class="back-footer">
      <div class="social-set" aria-label="Social profiles">
        <svg width="14" height="14" viewBox="0 0 14 14"><rect width="14" height="14" rx="2" fill="var(--on-green)"/></svg>
        <svg width="14" height="14" viewBox="0 0 14 14"><rect width="14" height="14" rx="2" fill="var(--on-green)"/></svg>
        <svg width="14" height="14" viewBox="0 0 14 14"><rect width="14" height="14" rx="2" fill="var(--on-green)"/></svg>
      </div>
      <p class="tagline">Live a life you don't need a holiday from</p>
      <div class="footer-rule"></div>
    </div>
  </section>

</main>
</body>
</html>
```